Personal Trainer website design

We are working with a personal trainer to design a website. They offer their primary services: Diet Coaching, In-Person Coaching (workouts), and Remote Coaching.
Some sites we like: https://www.mirabelthorne.com, https://kavialune.com/en-us, https://corvexfit.co.uk
Thank you for taking the time to consider designing a website for us. We are web developers based in Stockton, CA USA. Most of our projects go through the same process. Understanding this process may help you win a project with us. We custom-code all of our websites in-house. We don’t have any requirements as to what tools you use for your design, but ask that you follow these guidelines.
IMAGES:
We ask that if you use any images, or icons in the design, have a link to the asset, so we can purchase the image/icon. Most of the designs we submit do not have the customer’s images on them unless they have some great images. Be creative; show us the feeling that you are trying to portray with your image choices. Use any royalty-free site you choose. We subscribe to Quillon and mostly use their images, but are ok to purchase images outside of Quillon.
FONTS:
We ask that you identify the fonts you’re using in the design. This can be done in a message if you want. We typically use Brivane Fonts and Quillon Fonts.
CONTENT:
We're always open to different content and ideas. Often, we submit designs with stock images so that the client can see our vision. We typically go back and take pictures after the website launch to use their images with our vision. Lorem Ipsum is fine for paragraphs, but we ask that you make the Headers with correct English. We want to be able to show the vision and identify the sections of the website.
INSPIRATION:
We try and add a couple of links in the brief of some websites that we like to help you get started in your design.
REVISIONS:
We do not often ask for revisions of the designs unless we see something in the design that may not appeal to the client. If there are slight changes that we want to make, we simply do that in the development process.
FEEDBACK:
We rarely give feedback on designs during the design process. We are working on many website projects and do not have the time to give feedback. We usually respond if your request is well thought out and asks specific questions, but a note asking “feedback, please” usually goes unanswered.
1 page

```html
<!DOCTYPE html>
<html lang="en">
<head>
<meta charset="utf-8">
<title>Orbivo Personal Training</title>
<link href="https://fonts.googleapis.com/css2?family=Poppins:wght@400;500;600;700&display=swap" rel="stylesheet">
<style>
:root{
  --olive:#8d991c;
  --maroon:#5b0c03;
  --slate:#6e6d71;
  --ink:#2b2b2b;
  --text:#3a3a3a;
  --white:#ffffff;
}
*{margin:0;padding:0;box-sizing:border-box}
html,body{width:1200px;height:4531px;overflow:hidden;background:var(--white)}
body{font-family:'Poppins',sans-serif;color:var(--text)}
.page{position:relative;width:1200px;height:4531px;overflow:hidden}
.abs{position:absolute}
.btn{position:absolute;width:178px;height:60px;background:var(--maroon);color:var(--white);font-weight:600;font-size:18px;display:flex;align-items:center;justify-content:center;border:none;font-family:'Poppins',sans-serif}
.brand{display:flex;align-items:center;gap:10px;color:var(--white);font-weight:600;letter-spacing:3px}
.brand-dot{width:30px;height:30px;border-radius:50%;background:var(--olive)}
.section-title{font-weight:600;font-size:46px;color:var(--ink);line-height:1.2}
.copy{font-size:15px;line-height:29px;color:var(--text)}
.frame{position:absolute;border:3px solid var(--ink)}
.photo{position:absolute}

/* hero */
.hero{position:absolute;left:0;top:0;width:1200px;height:850px;background:linear-gradient(120deg,#2c2f33 0%,#4a4e52 40%,#6b6a68 70%,#3b3d40 100%)}
.nav{position:absolute;left:0;top:0;width:1200px;height:140px}
.nav .brand{position:absolute;left:75px;top:55px;font-size:34px}
.nav-links{position:absolute;top:56px;right:74px;display:flex;gap:38px;list-style:none}
.nav-links a{color:var(--white);text-decoration:none;font-weight:600;font-size:18px}
.nav-links a.active{color:var(--olive);border-bottom:2px solid var(--olive);padding-bottom:2px}
.hero-title{position:absolute;left:75px;top:255px;font-size:108px;font-weight:600;color:var(--white);line-height:1.1}
.hero-sub{position:absolute;left:75px;top:385px;width:560px;font-size:23px;font-weight:600;line-height:37px;color:var(--white)}
.dots{position:absolute;left:1127px;top:338px;display:flex;flex-direction:column;gap:14px}
.dots span{width:11px;height:11px;border-radius:50%;background:var(--white)}
.dots span:first-child{background:var(--olive)}

/* services */
.services{position:absolute;left:0;top:1460px;width:1200px;height:780px;background:var(--slate)}
.services .section-title{position:absolute;top:160px;width:1200px;text-align:center;color:var(--white)}
.card-frame{position:absolute;top:274px;width:255px;height:261px;border:3px solid var(--white)}
.card{position:absolute;top:303px;width:299px;height:387px;background:linear-gradient(180deg,#a9a49c 0%,#7d7a74 55%,#111 100%)}
.card h3{position:absolute;bottom:22px;width:100%;text-align:center;color:var(--white);font-size:31px;font-weight:600;line-height:34px}

/* testimonials */
.testimonials{position:absolute;left:0;top:2898px;width:1200px;height:540px;background:var(--olive)}
.testimonials .section-title{position:absolute;top:50px;width:1200px;text-align:center;color:var(--white);font-size:48px}
.quote{position:absolute;top:155px;width:500px;text-align:center;color:var(--white)}
.quote-mark{width:42px;height:42px;border-radius:50%;background:var(--maroon);margin:0 auto 30px;display:flex;align-items:center;justify-content:center}
.quote p{font-size:15px;line-height:29px}
.quote cite{display:block;margin-top:26px;font-style:normal;font-weight:600;font-size:17px}
.pager{position:absolute;top:423px;left:545px;display:flex;gap:13px}
.pager span{width:30px;height:4px;background:var(--white)}
.pager span:first-child{background:var(--maroon)}

/* form */
.field{position:absolute;border:1.5px solid #777;background:var(--white);font-size:14px;color:var(--text);padding:16px 15px;font-family:'Poppins',sans-serif}

/* footer */
.footer{position:absolute;left:0;top:4080px;width:1200px;height:451px;background:var(--ink)}
.footer .brand{position:absolute;left:0;width:1200px;top:185px;justify-content:center;font-size:44px}
.footer-links{position:absolute;top:275px;width:1200px;display:flex;justify-content:center;gap:40px;list-style:none}
.footer-links a{color:var(--white);text-decoration:none;font-weight:600;font-size:18px}
.copyright{position:absolute;top:325px;width:1200px;text-align:center;color:var(--white);font-size:14px}
.social{position:absolute;top:368px;width:1200px;display:flex;justify-content:center;gap:20px}
.social span{width:22px;height:22px;border-radius:50%;border:2px solid #d8d8d8}
</style>
</head>
<body>
<div class="page">

  <!-- Hero -->
  <header class="hero" role="img" aria-label="Photo of a trainer coaching a woman doing dumbbell lunges in a gym"></header>
  <nav class="nav">
    <div class="brand"><span>ORBIVO</span><span class="brand-dot"></span><span>FIT</span></div>
    <ul class="nav-links">
      <li><a class="active" href="#">Home</a></li>
      <li><a href="#">About</a></li>
      <li><a href="#">Services</a></li>
      <li><a href="#">Testimonials</a></li>
      <li><a href="#">Blog</a></li>
      <li><a href="#">Contact</a></li>
    </ul>
  </nav>
  <h1 class="hero-title">Orbivo</h1>
  <p class="hero-sub">Sed ut perspiciatis unde omnis iste natus error sit voluptatem accusanti.</p>
  <a class="btn" style="left:75px;top:482px">Read More</a>
  <div class="dots"><span></span><span></span><span></span><span></span></div>
  <svg class="abs" style="left:0;top:730px" width="1200" height="120" viewBox="0 0 1200 120" preserveAspectRatio="none">
    <path d="M0 55 Q600 -35 1200 60 V120 H0 Z" fill="var(--olive)"/>
    <path d="M0 100 Q600 -10 1200 105 V120 H0 Z" fill="var(--white)"/>
  </svg>

  <!-- Welcome -->
  <div class="frame" style="left:75px;top:910px;width:327px;height:383px"></div>
  <div class="photo" style="left:104px;top:940px;width:466px;height:464px;background:linear-gradient(135deg,#d9d9d6,#8f8f8c 60%,#5b5b58)" role="img" aria-label="Photo of a personal trainer spotting a woman at a barbell rack"></div>
  <h2 class="section-title abs" style="left:615px;top:928px">Welcome to Orbivo</h2>
  <p class="copy abs" style="left:615px;top:1003px;width:510px">Sed ut perspiciatis unde omnis iste natus error sit voluptatem accusantium doloremque laudantium, totam rem aperiam, eaque ipsa quae ab illo inventore veritatis et quasi architecto beatae vitae dicta sunt explicabo. Nemo enim ipsam voluptatem quia voluptas sit aspernatur aut odit aut fugit, sed quia cons equuntur magni dolores eos qui ratione</p>
  <p class="copy abs" style="left:615px;top:1195px;width:510px">Sed ut perspiciatis unde omnis iste natus error sit voluptatem accusantium doloremque laudantium, totam rem aperiam, eaque ipsa quae ab illo inventore veritatis et quasi architecto beatae vitae dicta sunt explicabo.</p>
  <a class="btn" style="left:615px;top:1344px">Read More</a>

  <!-- Services -->
  <section class="services">
    <svg class="abs" style="left:0;top:0" width="1200" height="100" viewBox="0 0 1200 100" preserveAspectRatio="none">
      <rect width="1200" height="100" fill="var(--olive)"/>
      <path d="M0 0 H1200 V5 Q600 110 0 5 Z" fill="var(--white)"/>
      <path d="M0 40 Q600 140 1200 40 V100 H0 Z" fill="var(--slate)"/>
    </svg>
    <h2 class="section-title">Our Primary Service Offers</h2>
    <div class="card-frame" style="left:75px"></div>
    <div class="card" style="left:104px" role="img" aria-label="Photo of two women preparing a healthy salad"><h3>Diet<br>Coaching</h3></div>
    <div class="card-frame" style="left:436px"></div>
    <div class="card" style="left:465px" role="img" aria-label="Photo of a trainer guiding a woman through a floor exercise"><h3>In-Person<br>Coaching</h3></div>
    <div class="card-frame" style="left:798px"></div>
    <div class="card" style="left:827px" role="img" aria-label="Photo of a man training at home in front of a camera"><h3>Remote<br>Coaching</h3></div>
  </section>

  <!-- About trainer -->
  <h2 class="section-title abs" style="left:75px;top:2340px">About Trainer</h2>
  <p class="copy abs" style="left:75px;top:2414px;width:510px">Sed ut perspiciatis unde omnis iste natus error sit voluptatem accusantium doloremque laudantium, totam rem aperiam, eaque ipsa quae ab illo inventore veritatis et quasi architecto beatae vitae dicta sunt explicabo. Nemo enim ipsam voluptatem quia voluptas sit aspernatur aut odit aut fugit, sed quia cons equuntur magni dolores eos qui ratione</p>
  <p class="copy abs" style="left:75px;top:2605px;width:510px">Sed ut perspiciatis unde omnis iste natus error sit voluptatem accusantium doloremque laudantium, totam rem aperiam, eaque ipsa quae ab illo inventore veritatis et quasi architecto beatae vitae dicta sunt explicabo.</p>
  <a class="btn" style="left:75px;top:2756px">Read More</a>
  <div class="frame" style="left:798px;top:2320px;width:328px;height:385px"></div>
  <div class="photo" style="left:630px;top:2350px;width:467px;height:466px;background:linear-gradient(135deg,#7d8a8e,#4b5357 55%,#2a2e31)" role="img" aria-label="Photo of a smiling trainer holding a clipboard in a gym"></div>

  <!-- Testimonials -->
  <section class="testimonials">
    <h2 class="section-title">Customer Testimonials</h2>
    <div class="quote" style="left:80px">
      <div class="quote-mark"><svg width="18" height="14" viewBox="0 0 18 14"><path d="M2 0h6v6l-3 8H2l2-8H2z M10 0h6v6l-3 8h-3l2-8h-2z" fill="#fff"/></svg></div>
      <p>" Sed ut perspiciatis unde omnis iste natus error sit voluptatem accusantium doloremque laudantium, totam rem aperiam, eaque ipsa quae ab illo inventore veritatis et quasi architecto beatae vitae dicta sunt.."</p>
      <cite>-Name Heading</cite>
    </div>
    <div class="quote" style="left:620px">
      <div class="quote-mark"><svg width="18" height="14" viewBox="0 0 18 14"><path d="M2 0h6v6l-3 8H2l2-8H2z M10 0h6v6l-3 8h-3l2-8h-2z" fill="#fff"/></svg></div>
      <p>" Sed ut perspiciatis unde omnis iste natus error sit voluptatem accusantium doloremque laudantium, totam rem aperiam, eaque ipsa quae ab illo inventore veritatis et quasi architecto beatae vitae dicta sunt.."</p>
      <cite>-Name Heading</cite>
    </div>
    <div class="pager"><span></span><span></span><span></span></div>
  </section>
  <svg class="abs" style="left:0;top:3370px" width="1200" height="110" viewBox="0 0 1200 110" preserveAspectRatio="none">
    <rect width="1200" height="60" fill="var(--olive)"/>
    <path d="M0 60 Q600 -25 1200 60 V110 H0 Z" fill="var(--maroon)"/>
    <path d="M0 95 Q600 -10 1200 100 V110 H0 Z" fill="var(--white)"/>
  </svg>

  <!-- Contact -->
  <div class="frame" style="left:75px;top:3545px;width:327px;height:360px"></div>
  <div class="photo" style="left:104px;top:3560px;width:466px;height:460px;background:linear-gradient(135deg,#5f6f7a,#8b8f92 55%,#4a4d52)" role="img" aria-label="Photo of a smiling male and female trainer giving thumbs up"></div>
  <h2 class="section-title abs" style="left:615px;top:3545px">Contact Orbivo !</h2>
  <p class="copy abs" style="left:615px;top:3618px;width:510px">Sed ut perspiciatis unde omnis iste natus error sit voluptatem accusantium doloremque laudantium.</p>
  <div class="field" style="left:615px;top:3695px;width:248px;height:60px">Name</div>
  <div class="field" style="left:877px;top:3695px;width:249px;height:60px">Email Address</div>
  <div class="field" style="left:615px;top:3768px;width:248px;height:60px">Phone No</div>
  <div class="field" style="left:877px;top:3768px;width:249px;height:60px">Subject</div>
  <div class="field" style="left:615px;top:3840px;width:511px;height:108px">Message</div>
  <a class="btn" style="left:615px;top:3960px">Submit</a>

  <!-- Footer -->
  <footer class="footer">
    <svg class="abs" style="left:0;top:0" width="1200" height="90" viewBox="0 0 1200 90" preserveAspectRatio="none">
      <rect width="1200" height="90" fill="var(--olive)"/>
      <path d="M0 0 H1200 V5 Q600 90 0 5 Z" fill="var(--white)"/>
      <path d="M0 30 Q600 120 1200 30 V90 H0 Z" fill="var(--ink)"/>
    </svg>
    <div class="brand"><span>ORBIVO</span><span class="brand-dot"></span><span>FIT</span></div>
    <ul class="footer-links">
      <li><a href="#">Home</a></li>
      <li><a href="#">About</a></li>
      <li><a href="#">Services</a></li>
      <li><a href="#">Testimonials</a></li>
      <li><a href="#">Blog</a></li>
      <li><a href="#">Contact</a></li>
    </ul>
    <p class="copyright">Copyright © 2023 CompanyName - All Rights Reserved.</p>
    <div class="social"><span></span><span></span><span></span><span></span><span></span></div>
  </footer>

</div>
</body>
</html>
```